Simple Commerce Site Design for Clothing & Goodies Brand

NOTE: ONLY COMMUNICATE THROUGH THIS WEBSITE DO NOT CONTACT ME PRIVATELY

I need a website centered around a premium clothing and merchandise brand, specializing in T-shirts and an array of appealing goodies including magnets, tote bags, and kitchen towels. This project aims to design a visually striking, simplistic, and user-friendly layout that captures the essence of our brand, "Les Vignerons de Sainte-Olivette."
Design Requirements
Page Designs
- Home Page: This page should feature a versatile promotional area to highlight special offers or featured products. The design of this zone should be elegant and integrate seamlessly with the rest of the page, drawing inspiration from but refining the approach seen on sites like https://brivo.com

- Product List: Dedicated pages for our primary offerings:

T-shirts in variations for Unisex-Men, Women (with a deep plunge), and Kids
Sweatshirts
Cotton Long Sleeves
Future expansions will include more colors, neck shapes, and items such as hats and polos.

- Goodies Page: Showcasing our range of premium goodies—magnets, tote bags, kitchen towels, and more—with a focus on product visuals and information.

- About/Contact Page: Sharing the story and values behind "Les Vignerons de Sainte-Olivette," along with contact information for customer inquiries.

Design Elements
Color Scheme: The brand's primary color is Panton 2955 (RGB: 33, 59, 99). This should be complemented with colors that enhance the premium feel and readability of the site.

Typography: Select fonts that reflect the brand's premium positioning, ensuring readability and elegance across different devices.

Navigation Bar: The layout must include a simple and straightforward navigation bar at the top of each page, facilitating easy access to all sections of the site without a search feature. This navigation bar should be minimalist and intuitive, allowing for a smooth user journey across the site.

Inspiration and Aesthetics
The site's aesthetic should draw inspiration from the provided examples below, aiming for a clean, modern, and user-centric design. While capturing the essence of those examples, our goal is to exceed them in usability and visual appeal, focusing on a layout that highlights our products and brand story in the most engaging manner.
https://brivo.com/
Similar but more simple design than: https://www.lumeo-mode.com/fr/fr/shop/homme

Industry/Entity Type

Clothing & Goodies Commerce site

Number of Pages Required

4 page

Requirements
Should not have
• Search, complex design

```html
<!DOCTYPE html>
<html lang="en">
<head>
<meta charset="utf-8">
<title>Les Vignerons de Sainte-Olivette</title>
<link rel="stylesheet" href="https://fonts.googleapis.com/css2?family=Montserrat:wght@300;400;500;600;700&family=Open+Sans:wght@400;600&display=swap">
<style>
:root{
  --navy:#213b63;
  --navy-deep:#1b2f52;
  --button:#2f5a9c;
  --ink:#1d1d1f;
  --muted:#6b6f78;
  --line:#c9cfd9;
  --panel:#f1f1f2;
  --white:#ffffff;
  --blob:#9cb0d4;
}
*{box-sizing:border-box;margin:0;padding:0}
html,body{width:1200px;height:3244px;overflow:hidden;background:var(--white);font-family:"Open Sans",Arial,sans-serif;color:var(--ink)}
.page{position:relative;width:1200px;height:3244px}
.heading{font-family:"Montserrat",Arial,sans-serif}
.btn{position:absolute;display:flex;align-items:center;justify-content:center;font-family:"Montserrat",Arial,sans-serif;font-weight:600;font-size:15px;letter-spacing:.5px;border-radius:22px}
.btn-solid{background:var(--button);color:var(--white)}
.btn-ghost{border:2px solid var(--white);color:var(--white);background:rgba(255,255,255,.05)}

/* header + hero */
.hero{position:absolute;left:0;top:0;width:1200px;height:688px;background:linear-gradient(100deg,#cfd0d2 0%,#aeb0b4 40%,#9ea1a6 62%,#c4c6c9 100%)}
.hero-figure{position:absolute;left:0;top:0;width:640px;height:688px;background:linear-gradient(180deg,#2a2c31 0%,#1e2024 100%);opacity:.9;border-radius:0 0 0 0}
.brand-badge{position:absolute;left:112px;top:12px;width:140px;height:140px;border-radius:50%;background:var(--white);display:flex;align-items:center;justify-content:center;text-align:center;padding:14px;font-family:"Montserrat",Arial,sans-serif;font-weight:700;font-size:13px;line-height:1.25;color:var(--navy);z-index:2}
.nav{position:absolute;top:34px;left:540px;display:flex;gap:56px;font-family:"Montserrat",Arial,sans-serif;font-size:15px;font-weight:500;color:var(--ink)}
.nav-icons{position:absolute;top:26px;left:990px;display:flex;gap:26px}
.hero-title{position:absolute;left:672px;top:292px;font-family:"Montserrat",Arial,sans-serif;font-size:46px;line-height:1.15;letter-spacing:1.5px;color:var(--ink);font-weight:700}
.hero-title span{font-weight:400}

/* products */
.products{position:absolute;top:688px;left:0;width:1200px;height:660px}
.section-title{font-family:"Montserrat",Arial,sans-serif;font-weight:700;font-size:36px;letter-spacing:1px;color:var(--ink)}
.products .section-title{position:absolute;left:112px;top:100px}
.filters{position:absolute;left:830px;top:98px;display:flex;gap:12px}
.filter{width:78px;height:38px;border:1px solid #8a8f98;border-radius:4px;display:flex;align-items:center;justify-content:center;font-family:"Montserrat",Arial,sans-serif;font-weight:600;font-size:13px}
.card{position:absolute;top:172px;width:280px}
.card-media{width:280px;height:300px;background:linear-gradient(180deg,#fafafa,#eeeff1);box-shadow:0 2px 10px rgba(0,0,0,.08);border-radius:4px;display:flex;align-items:center;justify-content:center}
.card-shape{width:160px;height:190px;border-radius:18px;background:linear-gradient(180deg,#26324a,#1a2337)}
.card-name{margin-top:26px;font-family:"Montserrat",Arial,sans-serif;font-size:16px;font-weight:500}
.card-price{margin-top:12px;font-family:"Montserrat",Arial,sans-serif;font-size:20px;font-weight:700}
.card-fav{position:absolute;right:8px;top:316px;width:34px;height:34px;border-radius:50%;background:#eef0f4;display:flex;align-items:center;justify-content:center}
.swatches{position:absolute;right:10px;top:370px;display:flex;gap:5px}
.swatches i{width:9px;height:9px;border-radius:50%;display:block}
.arrow{position:absolute;top:302px;width:40px;height:40px;border-radius:50%;border:1.5px solid #6f747c;display:flex;align-items:center;justify-content:center;background:var(--white)}

/* about */
.about{position:absolute;top:1348px;left:0;width:1200px;height:592px;background:linear-gradient(90deg,#1f3862 0%,#24406c 50%,#1d345b 100%)}
.about-bgphoto{position:absolute;left:220px;top:0;width:420px;height:592px;background:radial-gradient(ellipse at center,rgba(120,140,170,.28),rgba(33,59,99,0) 70%)}
.about .section-title{position:absolute;left:112px;top:128px;color:var(--white)}
.about-text{position:absolute;left:112px;top:188px;width:440px;font-size:14.5px;line-height:1.6;color:#e4e9f2}
.about-photo{position:absolute;left:632px;top:72px;width:456px;height:440px;background:linear-gradient(160deg,#a7b3bf 0%,#8b7768 45%,#8a2f35 70%,#6d5f58 100%)}

/* offers */
.offers{position:absolute;top:2048px;left:112px;width:976px;height:432px;background:var(--panel)}
.offers-blob{position:absolute;left:110px;top:86px}
.offers-art{position:absolute;left:50px;top:56px;width:240px;height:300px;background:linear-gradient(180deg,#efe6d2,#ddd1b8);border-radius:10px}
.offers .section-title{position:absolute;left:488px;top:120px;font-size:38px}
.offers-text{position:absolute;left:488px;top:184px;width:420px;font-size:14.5px;line-height:1.6;color:var(--muted)}

/* newsletter */
.newsletter-title{position:absolute;top:2568px;left:0;width:1200px;text-align:center;font-family:"Montserrat",Arial,sans-serif;font-weight:600;font-size:30px;letter-spacing:1px}
.field{position:absolute;border-bottom:1.5px solid var(--line);height:40px;font-size:14px;color:#33363c}
.field label{position:absolute;left:0;top:0}

/* footer */
.footer{position:absolute;top:2880px;left:0;width:1200px;height:364px;background:var(--navy)}
.footer-badge{position:absolute;left:160px;top:60px;width:160px;height:160px;border-radius:50%;background:var(--white);display:flex;align-items:center;justify-content:center;text-align:center;padding:18px;font-family:"Montserrat",Arial,sans-serif;font-weight:700;font-size:14px;line-height:1.25;color:var(--navy)}
.footer-col{position:absolute;top:40px;color:var(--white)}
.footer-col h4{font-family:"Montserrat",Arial,sans-serif;font-size:20px;font-weight:700;margin-bottom:18px}
.footer-col li{list-style:none;font-size:14px;line-height:1.9;display:flex;align-items:center;gap:12px}
.footer-col li svg{flex:none}
.contact li{align-items:flex-start;line-height:1.6;margin-bottom:14px;width:250px}
.copyright{position:absolute;left:112px;top:318px;color:var(--white);font-size:14px}
.partners{position:absolute;left:880px;top:300px;display:flex;gap:22px;align-items:center}
.partners i{display:block;background:#ffffff;border-radius:4px}
</style>
</head>
<body>
<div class="page">

  <section class="hero">
    <div class="hero-figure" role="img" aria-label="Photo of two people wearing black hooded sweatshirts with the brand print"></div>
    <div class="brand-badge">Les Vignerons de Sainte-Olivette</div>
    <nav class="nav"><span>HOME</span><span>PRODUCTS</span><span>GOODIES</span><span>ABOUT</span></nav>
    <div class="nav-icons">
      <svg width="34" height="34" viewBox="0 0 34 34" fill="none" stroke="#213b63" stroke-width="2.4"><circle cx="17" cy="17" r="14"/><circle cx="17" cy="14" r="5"/><path d="M8 27c3-5 15-5 18 0"/></svg>
      <svg width="36" height="34" viewBox="0 0 36 34" fill="none" stroke="#213b63" stroke-width="2.6"><path d="M2 4h6l4 18h18l4-13H10"/><circle cx="14" cy="29" r="2.5"/><circle cx="28" cy="29" r="2.5"/></svg>
    </div>
    <h1 class="hero-title">LES VIGNERONS<br><span>DE SAINTE-OLIVETTE</span></h1>
    <div class="btn btn-solid" style="left:688px;top:470px;width:96px;height:42px">MALE</div>
    <div class="btn btn-ghost" style="left:808px;top:470px;width:104px;height:42px">WOMEN</div>
  </section>

  <section class="products">
    <h2 class="section-title">OUR PRODUCTS</h2>
    <div class="filters"><div class="filter">MEN</div><div class="filter">WOMAN</div><div class="filter">KIDS</div></div>

    <div class="arrow" style="left:44px"><svg width="14" height="14" viewBox="0 0 14 14" fill="none" stroke="#555" stroke-width="2"><path d="M9 2L4 7l5 5"/></svg></div>
    <div class="arrow" style="left:1116px"><svg width="14" height="14" viewBox="0 0 14 14" fill="none" stroke="#555" stroke-width="2"><path d="M5 2l5 5-5 5"/></svg></div>

    <article class="card" style="left:112px">
      <div class="card-media" role="img" aria-label="Product photo of a navy long-sleeve cotton shirt"><div class="card-shape"></div></div>
      <p class="card-name">Cotton Long Sleeves</p>
      <p class="card-price">$50</p>
      <div class="card-fav"><svg width="14" height="14" viewBox="0 0 14 14" fill="none" stroke="#213b63" stroke-width="1.6"><path d="M3 3l8 8M11 3l-8 8"/></svg></div>
      <div class="swatches"><i style="background:#e0b23a"></i><i style="background:#213b63"></i><i style="background:#213b63"></i><i style="background:#213b63"></i></div>
    </article>

    <article class="card" style="left:420px">
      <div class="card-media" role="img" aria-label="Product photo of a navy women's t-shirt, back view"><div class="card-shape" style="width:140px;height:180px"></div></div>
      <p class="card-name">6 t shirt VSO femme dos</p>
      <p class="card-price">$50</p>
      <div class="card-fav"><svg width="14" height="14" viewBox="0 0 14 14" fill="none" stroke="#213b63" stroke-width="1.6"><path d="M3 3l8 8M11 3l-8 8"/></svg></div>
      <div class="swatches"><i style="background:#213b63"></i><i style="background:#213b63"></i><i style="background:#213b63"></i><i style="background:#213b63"></i></div>
    </article>

    <article class="card" style="left:728px">
      <div class="card-media" role="img" aria-label="Product photo of a navy kids t-shirt"><div class="card-shape" style="width:150px;height:150px;background:linear-gradient(180deg,#2e3b78,#222c5c)"></div></div>
      <p class="card-name">24 t shirt Kid</p>
      <p class="card-price">$50</p>
      <div class="card-fav"><svg width="14" height="14" viewBox="0 0 14 14" fill="none" stroke="#213b63" stroke-width="1.6"><path d="M3 3l8 8M11 3l-8 8"/></svg></div>
      <div class="swatches"><i style="background:#e0b23a"></i><i style="background:#4caf50"></i><i style="background:#213b63"></i><i style="background:#213b63"></i></div>
    </article>
  </section>

  <section class="about">
    <div class="about-bgphoto" role="img" aria-label="Faint background photo of people in brand sweatshirts"></div>
    <h2 class="section-title">ABOUT US</h2>
    <p class="about-text">Lorem ipsum dolor sit amet, consectetur adipiscing elit, sed do eiusmod tempor incididunt ut labore et dolore magna aliqua. Ut enim ad minim veniam, quis nostrud exercitation ullamco laboris nisi ut aliquip ex ea commodo consequat. Duis aute irure dolor in reprehenderit in voluptate velit esse cillum dolore eu fugiat nulla pariatur. Excepteur sint occaecat cupidatat non proident, sunt in culpa qui officia deserunt mollit anim id est laborum.</p>
    <div class="btn btn-ghost" style="left:112px;top:412px;width:140px;height:44px;font-size:13px">LEARN MORE</div>
    <div class="about-photo" role="img" aria-label="Photo of two smiling people in knit beanies and a red sweater outdoors"></div>
  </section>

  <section class="offers">
    <svg class="offers-blob" width="340" height="290" viewBox="0 0 340 290"><path d="M60 40C130-10 290 0 325 90c30 80-20 170-110 190C120 300 20 250 8 170 0 120 20 70 60 40z" fill="#9cb0d4"/></svg>
    <div class="offers-art" role="img" aria-label="Illustration of a canvas tote bag with the brand print"></div>
    <h2 class="section-title">SPECIAL OFFERS</h2>
    <p class="offers-text">Lorem ipsum dolor sit amet, consectetur adipiscing elit, sed do eiusmod tempor incididunt ut labore et dolore magna aliqua.</p>
    <div class="btn btn-solid" style="left:488px;top:272px;width:96px;height:40px;font-size:13px">SHOP</div>
  </section>

  <h2 class="newsletter-title">RECEIVE EXCLUSIVE PRODUCT AND PREVIEWS</h2>
  <div class="field" style="left:320px;top:2644px;width:252px"><label>First Name</label></div>
  <div class="field" style="left:628px;top:2644px;width:252px"><label>Last Name</label></div>
  <div class="field" style="left:320px;top:2700px;width:560px"><label>Email</label></div>
  <div class="btn btn-solid" style="left:544px;top:2760px;width:112px;height:42px;font-size:13px">SUBMIT</div>

  <footer class="footer">
    <div class="footer-badge">Les Vignerons de Sainte-Olivette</div>
    <div class="footer-col" style="left:432px">
      <h4>Quick Links</h4>
      <ul>
        <li><svg width="8" height="10" viewBox="0 0 8 10"><path d="M1 1l6 4-6 4z" fill="#fff"/></svg>Home</li>
        <li><svg width="8" height="10" viewBox="0 0 8 10"><path d="M1 1l6 4-6 4z" fill="#fff"/></svg>Products</li>
        <li><svg width="8" height="10" viewBox="0 0 8 10"><path d="M1 1l6 4-6 4z" fill="#fff"/></svg>Goodies</li>
        <li><svg width="8" height="10" viewBox="0 0 8 10"><path d="M1 1l6 4-6 4z" fill="#fff"/></svg>About</li>
      </ul>
    </div>
    <div class="footer-col" style="left:640px">
      <h4>Our Company</h4>
      <ul>
        <li><svg width="8" height="10" viewBox="0 0 8 10"><path d="M1 1l6 4-6 4z" fill="#fff"/></svg>Terms &amp; Conditions</li>
        <li><svg width="8" height="10" viewBox="0 0 8 10"><path d="M1 1l6 4-6 4z" fill="#fff"/></svg>Privacy Policy</li>
        <li><svg width="8" height="10" viewBox="0 0 8 10"><path d="M1 1l6 4-6 4z" fill="#fff"/></svg>About Us</li>
        <li><svg width="8" height="10" viewBox="0 0 8 10"><path d="M1 1l6 4-6 4z" fill="#fff"/></svg>Support</li>
      </ul>
    </div>
    <div class="footer-col contact" style="left:864px">
      <h4>Contact us</h4>
      <ul>
        <li><svg width="14" height="18" viewBox="0 0 14 18"><path d="M7 1a6 6 0 0 0-6 6c0 4.5 6 10 6 10s6-5.5 6-10a6 6 0 0 0-6-6z" fill="#fff"/><circle cx="7" cy="7" r="2.2" fill="#213b63"/></svg>Lorem ipsum dolor sit amet, consectetur adipiscing</li>
        <li><svg width="16" height="16" viewBox="0 0 16 16"><path d="M3 1h3l1.5 4-2 1.2a9 9 0 0 0 4.3 4.3L11 8.5l4 1.5v3a2 2 0 0 1-2 2A12 12 0 0 1 1 3a2 2 0 0 1 2-2z" fill="#fff"/></svg>+33 4 90 12 34 56</li>
        <li><svg width="16" height="14" viewBox="0 0 16 14"><rect x="1" y="2" width="14" height="10" rx="1" fill="#fff"/><path d="M1.5 2.5L8 8l6.5-5.5" fill="none" stroke="#213b63" stroke-width="1.4"/></svg>info@vignerons-olivette.com</li>
      </ul>
    </div>
    <p class="copyright">©Copyrights 2024 Les Vignerons de Sainte-Olivette &nbsp;|&nbsp; All Rights Reserved</p>
    <div class="partners">
      <i style="width:70px;height:22px"></i>
      <i style="width:60px;height:22px"></i>
      <i style="width:56px;height:22px"></i>
      <i style="width:26px;height:14px"></i>
    </div>
  </footer>

</div>
</body>
</html>
```